Lucky Harbour Fun Casino Entertainment

Looking to update my business card and make it look more modern, stand out and eye catching.
We are are fun casino business in Australia (primarily Sydney). Blackjack and Roulette are our most popular games although we have pretty much every game available for hire that you would find in a real casino. The final design would need to be sleek and appeal to the more upmarket corporate sector.
We mainly cater for Corporate Events, Private Parties, Fundraising Events, Team Building, Poker Tournaments
I think I'd prefer the colour Black.

Target Market(s)

High-end Corporate

Industry/Entity Type

Events

Contact Information for Business Card

Rob Kendall
Director
1300 482 617
0433 728 591
info@luckyharbour.com.au
www.luckyharbour.com.au
Facebook & Instagram @luckyharbourevents (proper social icons preferred)

Colors
000000
0255a3

Requirements
Must have
• Front side:
• Logo
• Contact details
• 'Sydney's Finest Fun Casino Hosts'
• Back:
• Logo
Nice to have
• Back:
• Corporate Events
• Private Parties
• Poker Tournaments
• Fundraising
• Props & Theming
• Photo Booth
• Horse Racing Events
• The Vegas Sign attached, maybe on the back of the card in the background...?

```html
<!DOCTYPE html>
<html lang="en">
<head>
<meta charset="utf-8">
<title>Lucky Harbour Fun Casino Entertainment – Business Card</title>
<link rel="stylesheet" href="https://fonts.googleapis.com/css2?family=Open+Sans:wght@400;600;700&family=Great+Vibes&display=swap">
<style>
  :root {
    --stage: #2b2d31;
    --card-dark: #1c1c1e;
    --card-dark-top: #3a3a3c;
    --paper: #ffffff;
    --amber: #f7a823;
    --amber-light: #fcc24a;
    --ink: #1a1a1a;
    --ink-soft: #666666;
    --hatch: #c9c9c9;
  }
  * { box-sizing: border-box; margin: 0; padding: 0; }
  html, body { width: 1200px; height: 900px; overflow: hidden; }
  body {
    background: var(--stage);
    font-family: "Open Sans", Arial, sans-serif;
    position: relative;
  }
  .card {
    position: absolute;
    border-radius: 22px;
    overflow: hidden;
    background: var(--paper);
    box-shadow: 0 18px 40px rgba(0,0,0,.45);
  }

  /* ---------- Front (portrait) ---------- */
  .card-front { left: 90px; top: 140px; width: 350px; height: 620px; }
  .front-head {
    position: absolute; left: 0; top: 0; width: 100%; height: 270px;
    background: linear-gradient(160deg, var(--card-dark-top), var(--card-dark) 70%);
    display: flex; flex-direction: column; align-items: center; justify-content: center; gap: 18px;
  }
  .brand { display: flex; align-items: center; gap: 10px; }
  .brand-dot { width: 22px; height: 22px; border-radius: 50%; background: var(--amber); }
  .brand-name {
    font-weight: 700; color: var(--amber); letter-spacing: .5px; text-transform: uppercase;
    white-space: nowrap;
  }
  .card-front .brand-name { font-size: 28px; }
  .tagline { font-family: "Great Vibes", cursive; font-size: 24px; white-space: nowrap; }
  .card-front .tagline { color: #e8e8e8; }

  .divider { position: absolute; left: 0; width: 100%; height: 22px; }
  .card-front .divider { top: 270px; }
  .divider .tab-left, .divider .tab-right {
    position: absolute; top: 0; height: 100%;
    background: linear-gradient(90deg, var(--amber), var(--amber-light));
  }
  .divider .hatch {
    position: absolute; top: 0; height: 100%;
    background: repeating-linear-gradient(135deg, var(--hatch) 0 1.5px, transparent 1.5px 5px);
  }
  .card-front .tab-left { left: 0; width: 70px; }
  .card-front .hatch { left: 70px; width: 210px; }
  .card-front .tab-right { right: 0; width: 70px; }

  .front-body { position: absolute; left: 40px; right: 30px; top: 320px; }
  .person-name { font-size: 30px; font-weight: 700; color: var(--amber); line-height: 1.1; }
  .person-role {
    font-size: 16px; color: var(--ink-soft); padding-bottom: 8px;
    border-bottom: 2px solid var(--amber); display: inline-block; width: 120px; margin-bottom: 18px;
  }
  .contact-list { list-style: none; display: flex; flex-direction: column; gap: 9px; }
  .contact-item { display: flex; align-items: flex-start; gap: 10px; font-size: 14px; color: var(--ink-soft); white-space: nowrap; }
  .contact-item.address { font-weight: 700; color: var(--ink); font-size: 15px; line-height: 1.35; }
  .icon-tag {
    flex: 0 0 20px; width: 20px; height: 20px; border-radius: 3px; background: var(--amber);
    display: flex; align-items: center; justify-content: center;
  }
  .icon-tag svg { width: 12px; height: 12px; }
  .phones { gap: 10px; align-items: center; }
  .phones .gap { width: 4px; }

  /* ---------- Back (landscape) ---------- */
  .card-back { left: 520px; top: 270px; width: 620px; height: 354px; }
  .back-head {
    position: absolute; left: 0; top: 0; width: 100%; height: 200px;
    display: flex; flex-direction: column; align-items: center; justify-content: center; gap: 14px;
    padding-left: 60px;
  }
  .card-back .brand-name { font-size: 38px; }
  .card-back .brand-dot { width: 28px; height: 28px; }
  .card-back .tagline { color: var(--ink); font-size: 30px; }
  .card-back .divider { top: 200px; }
  .card-back .tab-left { left: 0; width: 150px; }
  .card-back .hatch { left: 150px; width: 310px; }
  .card-back .tab-right { right: 0; width: 160px; }
  .back-foot {
    position: absolute; left: 0; top: 222px; width: 100%; bottom: 0;
    background: var(--card-dark);
    display: flex; flex-direction: column; justify-content: center; gap: 10px; padding: 0 30px;
  }
  .services { list-style: none; display: flex; flex-wrap: nowrap; white-space: nowrap; font-size: 15px; color: #f1f1f1; }
  .services li + li::before { content: "/"; color: var(--amber); margin: 0 8px; }
</style>
</head>
<body>

<section class="card card-front" aria-label="Business card front">
  <header class="front-head">
    <div class="brand">
      <span class="brand-dot"></span>
      <span class="brand-name">Lucky Harbour</span>
    </div>
    <p class="tagline">Sydney's Finest Fun Casino Hosts</p>
  </header>
  <div class="divider"><span class="tab-left"></span><span class="hatch"></span><span class="tab-right"></span></div>
  <div class="front-body">
    <h1 class="person-name">Rob Kendall</h1>
    <p class="person-role">Director</p>
    <ul class="contact-list">
      <li class="contact-item address">
        <span class="icon-tag"><svg viewBox="0 0 12 12"><path d="M6 1a3.5 3.5 0 0 0-3.5 3.5C2.5 7.5 6 11 6 11s3.5-3.5 3.5-6.5A3.5 3.5 0 0 0 6 1zm0 5a1.4 1.4 0 1 1 0-2.8A1.4 1.4 0 0 1 6 6z" fill="#fff"/></svg></span>
        <span>5/27 Harbour Street,<br>Rosehill 2142</span>
      </li>
      <li class="contact-item phones">
        <span class="icon-tag"><svg viewBox="0 0 12 12"><path d="M3 1.5l1.6 2.2-.9 1.1c.6 1.3 1.6 2.3 2.9 2.9l1.1-.9 2.2 1.6-.8 1.9C5.5 10.5 1.5 6.5 1.7 2.3z" fill="#fff"/></svg></span>
        <span>1300 482 617</span>
        <span class="gap"></span>
        <span class="icon-tag"><svg viewBox="0 0 12 12"><rect x="3.5" y="1" width="5" height="10" rx="1" fill="#fff"/><rect x="4.5" y="2.2" width="3" height="6" fill="#f7a823"/></svg></span>
        <span>0433 728 591</span>
      </li>
      <li class="contact-item">
        <span class="icon-tag"><svg viewBox="0 0 12 12"><rect x="1" y="2.5" width="10" height="7" rx="1" fill="#fff"/><path d="M1.5 3l4.5 3.5L10.5 3" stroke="#f7a823" fill="none"/></svg></span>
        <span>info@luckyharbour.com.au</span>
      </li>
      <li class="contact-item">
        <span class="icon-tag"><svg viewBox="0 0 12 12"><circle cx="6" cy="6" r="4.5" fill="none" stroke="#fff" stroke-width="1.2"/><path d="M1.5 6h9M6 1.5c-2 2.5-2 6.5 0 9M6 1.5c2 2.5 2 6.5 0 9" stroke="#fff" fill="none"/></svg></span>
        <span>www.luckyharbour.com.au</span>
      </li>
      <li class="contact-item">
        <span class="icon-tag"><svg viewBox="0 0 12 12"><circle cx="6" cy="6" r="4" fill="#fff"/></svg></span>
        <span>@luckyharbourevents</span>
      </li>
      <li class="contact-item">
        <span class="icon-tag"><svg viewBox="0 0 12 12"><rect x="2" y="2" width="8" height="8" rx="1.5" fill="#fff"/></svg></span>
        <span>@luckyharbourevents</span>
      </li>
    </ul>
  </div>
</section>

<section class="card card-back" aria-label="Business card back">
  <header class="back-head">
    <div class="brand">
      <span class="brand-dot"></span>
      <span class="brand-name">Lucky Harbour</span>
    </div>
    <p class="tagline">Sydney's Finest Fun Casino Hosts</p>
  </header>
  <div class="divider"><span class="tab-left"></span><span class="hatch"></span><span class="tab-right"></span></div>
  <footer class="back-foot">
    <ul class="services">
      <li>Corporate Events</li><li>Private Parties</li><li>Poker Tournaments</li>
    </ul>
    <ul class="services">
      <li>Fundraising</li><li>Props &amp; Theming</li><li>Photo Booth</li><li>Horse Racing Events</li>
    </ul>
  </footer>
</section>

</body>
</html>
```